We are a new company with 2 divisions a medical research and medical product sales. We need a company logo and Business Cards. The design files need to be provided to us in Adobe Photoshop CS 5.1.

Target Market(s)

Medical Community

Industry/Entity Type

Medical

Contact Information for Business Card

Company Name - Harrowgate Lifesciences LLC
Company Address 4127 Larkspur Ave Suite 7, Tallow Creek Fl 32614

Requirements
Must have
• The design files need to be provided to us in Adobe Photoshop CS 5.1.

```html
<!DOCTYPE html>
<html lang="en">
<head>
<meta charset="utf-8">
<title>Harrowgate Lifesciences LLC – Business Card</title>
<link rel="stylesheet" href="https://fonts.googleapis.com/css2?family=Tinos:wght@400;700&display=swap">
<style>
  :root {
    --canvas: #eef0f2;
    --card: #ffffff;
    --brand-blue: #1c6fa8;
    --band-blue: #1f8fc4;
    --band-teal: #2aa8b8;
    --band-green: #7cc242;
    --ink: #1a1a1a;
  }
  * { margin: 0; padding: 0; box-sizing: border-box; }
  html, body {
    width: 1200px; height: 900px; overflow: hidden;
    background: var(--canvas);
    font-family: "Tinos", "Times New Roman", serif;
  }
  .card {
    position: absolute; left: 100px; top: 145px;
    width: 1000px; height: 610px;
    background: var(--card);
    overflow: hidden;
    box-shadow: 0 6px 24px rgba(0,0,0,0.12);
  }
  .card__band { position: absolute; inset: 0; width: 100%; height: 100%; }
  .brand {
    position: absolute; left: 40px; top: 50px;
    display: flex; align-items: center; gap: 28px;
  }
  .brand__mark {
    flex: none;
    width: 170px; height: 170px; border-radius: 50%;
    background: var(--brand-blue);
  }
  .brand__name {
    color: var(--brand-blue);
    font-size: 46px; line-height: 1.05; font-weight: 400;
    text-transform: uppercase; letter-spacing: 0.5px;
  }
  .person { position: absolute; left: 53px; top: 300px; }
  .person__name {
    color: var(--brand-blue); font-weight: 700; font-size: 42px; line-height: 1.1;
  }
  .person__role { color: var(--ink); font-size: 29px; line-height: 1.2; }
  .contact {
    position: absolute; left: 53px; top: 420px;
    list-style: none; color: var(--ink);
    font-size: 30px; line-height: 37px;
  }
</style>
</head>
<body>
  <article class="card">
    <svg class="card__band" viewBox="0 0 1000 610" aria-hidden="true">
      <defs>
        <linearGradient id="bandGradient" x1="0" y1="0" x2="0.2" y2="1">
          <stop offset="0" stop-color="#1f8fc4"/>
          <stop offset="0.45" stop-color="#2aa8b8"/>
          <stop offset="1" stop-color="#7cc242"/>
        </linearGradient>
      </defs>
      <path d="M490 0 C700 40 830 200 845 360 C852 450 840 540 820 610 L1000 610 L1000 0 Z" fill="url(#bandGradient)"/>
    </svg>

    <header class="brand">
      <span class="brand__mark"></span>
      <h1 class="brand__name">Harrowgate<br>Lifesciences LLC.</h1>
    </header>

    <section class="person">
      <p class="person__name">John Doe</p>
      <p class="person__role">Chief Executive Officer</p>
    </section>

    <ul class="contact">
      <li>4127 Larkspur Ave Suite 7</li>
      <li>Tallow Creek Fl 32614</li>
      <li>Phone: 123 456 789</li>
      <li>Email: yourname@yourcompany.com</li>
      <li>www.yourcompany.com</li>
    </ul>
  </article>
</body>
</html>
```